Award-winnning Estate Agent needs a premium version of their 'For Sale' board design

We need a premium option for our 'For Sale' board design. We have a standard board that is attached to this brief, but were are looking to have a premium design version that we will use when selling exclusive properties. Our company name is Harbourline Vale Estates and the name for this is exclusive selection is: 'The Harbourline Collection'. The design needs to work with our current brand, but have a distinctive PREMIUM feel to it. I have uploaded the barnd guidelines and also some of the exisisting logo variations. We do NOT need a new logo but feel free to play around with colours, fonts, sizes etc. for the sign.

Target Market(s)

Property buyers & house hunters

Industry/Entity Type

Real Estate - Residential Property

Font styles to use
Sans Serif

Requirements
Must have
• A premium fee, must be square design, must be easy to read when driving past the sign
Nice to have
• I'm open ot ideas

```html
<!DOCTYPE html>
<html lang="en">
<head>
<meta charset="utf-8">
<title>The Harbourline Collection – Premium For Sale Board</title>
<link rel="stylesheet" href="https://fonts.googleapis.com/css2?family=Montserrat:wght@500;700;800&display=swap">
<style>
  :root {
    --navy: #23246a;
    --frame: #2b2d7c;
    --red: #b2252b;
    --blue: #1d7fc0;
    --white: #ffffff;
    --backdrop: #eceef2;
  }
  * { margin: 0; padding: 0; box-sizing: border-box; }
  html, body {
    width: 1200px;
    height: 735px;
    overflow: hidden;
    background: var(--backdrop);
    font-family: "Montserrat", Arial, sans-serif;
  }
  .canvas {
    width: 1200px;
    height: 735px;
    display: flex;
    align-items: center;
    justify-content: center;
  }
  .board {
    width: 680px;
    height: 680px;
    background: var(--frame);
    padding: 20px;
  }
  .board-face {
    position: relative;
    width: 100%;
    height: 100%;
    background: var(--white);
    display: flex;
    flex-direction: column;
    align-items: center;
    padding: 46px 40px 40px;
  }
  .keyline {
    position: absolute;
    inset: 12px;
    border: 2px solid var(--navy);
    pointer-events: none;
  }
  .brand {
    display: flex;
    flex-direction: column;
    align-items: center;
    gap: 20px;
  }
  .brand-mark {
    width: 56px;
    height: 56px;
    background: var(--blue);
  }
  .brand-name {
    color: var(--navy);
    font-weight: 700;
    font-size: 33px;
    line-height: 1.2;
    white-space: nowrap;
  }
  .brand-rule {
    width: 120px;
    height: 3px;
    background: var(--red);
  }
  .bands {
    width: 100%;
    margin-top: 34px;
    display: flex;
    flex-direction: column;
  }
  .band {
    width: 100%;
    color: var(--white);
    display: flex;
    align-items: center;
    justify-content: center;
    line-height: 1;
    white-space: nowrap;
  }
  .band-sale {
    background: var(--red);
    height: 124px;
    font-size: 82px;
    font-weight: 800;
    letter-spacing: 2px;
  }
  .band-phone {
    background: var(--blue);
    height: 96px;
    font-size: 56px;
    font-weight: 700;
    letter-spacing: 1px;
  }
  .web-address {
    margin-top: auto;
    color: var(--navy);
    font-weight: 700;
    font-size: 25px;
    white-space: nowrap;
  }
</style>
</head>
<body>
  <main class="canvas">
    <section class="board">
      <div class="board-face">
        <span class="keyline" aria-hidden="true"></span>
        <header class="brand">
          <span class="brand-mark" aria-hidden="true"></span>
          <h1 class="brand-name">The Harbourline Collection</h1>
          <span class="brand-rule" aria-hidden="true"></span>
        </header>
        <div class="bands">
          <p class="band band-sale">FOR SALE</p>
          <p class="band band-phone">01632 960481</p>
        </div>
        <p class="web-address">www.harbourlinevaleestates.co.uk</p>
      </div>
    </section>
  </main>
</body>
</html>
```